Wordpress Design Project

We are an online jewellery business currently trading entirely online through internet auctions.

We are revamping our online operations. We want to launch our website. Which will incorporate extensive social media integration. Chatterloop, Blogging to chatterloop as well as Boardquill. These need to be linked (some and/or interactive).

We want to collect subscriptions and collate emails/info.

There may also be video uploads of our stock.

Whilst we are Sydney based we see ourselves as a global business.

We sell High End exclusive designer jewellery.
Often bespoke pieces of diamond jewellery.

Words that some up our brand personality
Savvy, Stylish, Confident, Approachable

About our style
Ensuring not only that our designs and jewellery have a certain sense of classic or fashion-driven style, but expressing style and beauty through all touch points. We understand that style is not only about what you wear, but how you carry yourself.

About our company mission
Make precious jewellery an affordable luxury for stylish, savvy buyers
Create products that we're proud to sell and that customers desire, treasure and proudly wear.

KEY FOCUS/OUTCOME:

We require a stylish, clean, visually easy to navigate website. Main aim of the site is to showcase products. Not a shop per se. Ultimate goal is to engage the viewer to ask us to make something special for them. Not a huge budget. WE are a small business. But we make beautiful fine jewellery. Focus on Blog, social media interactions important, Innovative WORDPRESS design. Think special. We want to be inspired as we are inspired by some of the links we've presented here. They give a great overall feel of what we are looking for.

We require full implementation to be delivered.

http://www.tarvoselk.com/
http://www.merovatrikes.com/
http://www.fenwardspirit.com/cocktails/
www.plomarn.ch
http://www.vuralette.fr/en

SEO expertise as well as adaptation across all mobile devices/tablets.

Requirements
Must have
• Social Media, Blog, unique design (not same-same) Has to feel bespoke. 48 hour "buy it now" feature. Like a daily deal function with the ability to check out through CoinVeil. One high ticket item per day. Easy for us to manipulate/upload to website. User friendly.
Fast website. Not slow.
Should not have
• -should not look like a traditional shopping cart.

```html
<!DOCTYPE html>
<html lang="en">
<head>
<meta charset="utf-8">
<title>Varenna — designer jewellery</title>
<link rel="stylesheet" href="https://fonts.googleapis.com/css2?family=Fjord+One&family=Ubuntu:wght@400;500&display=swap">
<style>
  :root {
    --ink: #111111;
    --text: #333333;
    --muted: #666666;
    --line: #d4d4d4;
    --band: #ececec;
    --footer: #f3f3f3;
    --menu: #7a7a7a;
    --menu-line: #9a9a9a;
    --arrow-box: #444444;
    --white: #ffffff;
    --search: #3a3a3a;
  }
  * { box-sizing: border-box; margin: 0; padding: 0; }
  html, body { width: 1178px; height: 1200px; overflow: hidden; }
  body { font-family: "Ubuntu", sans-serif; color: var(--text); background: var(--white); position: relative; }
  a { color: inherit; text-decoration: none; }

  .topbar { position: absolute; left: 0; top: 0; width: 1178px; height: 67px; background: var(--ink); }
  .brand-name { position: absolute; left: 128px; top: 16px; font-family: "Ubuntu", sans-serif; font-size: 34px; font-weight: 400; letter-spacing: 2px; color: var(--white); line-height: 36px; }
  .brand-tag { position: absolute; left: 128px; top: 80px; font-family: "Ubuntu", sans-serif; font-size: 16px; font-weight: 400; color: var(--ink); }

  .account-links { position: absolute; right: 264px; top: 27px; font-size: 11px; color: #dddddd; display: flex; gap: 12px; white-space: nowrap; }
  .account-links .sep { color: #888; }
  .search { position: absolute; left: 927px; top: 21px; width: 124px; height: 25px; border-radius: 4px; background: var(--search); }
  .search svg { position: absolute; right: 6px; top: 5px; }

  .utility { position: absolute; top: 90px; right: 127px; font-size: 11px; color: var(--muted); display: flex; align-items: center; gap: 10px; white-space: nowrap; }
  .utility b { color: var(--ink); font-weight: 500; }
  .follow-names { display: flex; gap: 6px; color: var(--ink); font-size: 10px; }

  .nav { position: absolute; left: 0; top: 123px; width: 1178px; height: 52px; background: var(--band); border-bottom: 1px solid var(--line); }
  .nav ul { list-style: none; position: absolute; left: 128px; top: 0; width: 922px; height: 52px; display: flex; justify-content: space-between; align-items: center; font-size: 13px; color: var(--ink); }
  .nav li { display: flex; align-items: center; gap: 9px; white-space: nowrap; }
  .caret { width: 12px; height: 2px; background: #777; display: inline-block; }

  .hero { position: absolute; left: 0; top: 175px; width: 1178px; height: 532px; background: radial-gradient(ellipse at 35% 45%, #fafafa 0%, #e2e2e2 55%, #cfcfcf 100%); }
  .submenu { position: absolute; left: 128px; top: 0; width: 151px; list-style: none; background: var(--menu); z-index: 2; }
  .submenu li { height: 28px; border-bottom: 1px solid var(--menu-line); color: var(--white); font-size: 11px; display: flex; align-items: center; padding-left: 12px; gap: 9px; }
  .slide-arrow { position: absolute; top: 231px; width: 56px; height: 56px; background: var(--arrow-box); }
  .slide-arrow.prev { left: 128px; }
  .slide-arrow.next { left: 994px; }
  .hero-copy { position: absolute; left: 676px; top: 280px; font-family: "Fjord One", serif; color: #555; }
  .hero-copy .lead { font-size: 40px; color: #444; line-height: 44px; }
  .hero-copy .sub { font-size: 30px; line-height: 35px; color: #777; }
  .hero-copy .note { font-size: 26px; line-height: 38px; color: #555; }

  .showcase-arrow { position: absolute; top: 797px; }
  .tile { position: absolute; top: 730px; width: 294px; height: 197px; }
  .tile.ring { left: 128px; background: radial-gradient(ellipse at 50% 45%, #9a9a9a 0%, #3a3a3a 40%, #050505 75%); }
  .tile.watch { left: 442px; background: radial-gradient(circle at 50% 50%, #d7c48a 0%, #b49a5c 40%, #5a544b 70%, #45423e 100%); }
  .tile.bracelet { left: 756px; background: linear-gradient(180deg, #050505 0%, #050505 32%, #8c8892 50%, #3a3840 62%, #050505 80%); }
  .tile-label { position: absolute; left: 0; width: 100%; top: 78px; text-align: center; color: var(--white); font-size: 20px; font-weight: 500; letter-spacing: 0.5px; }
  .quick-view { position: absolute; left: 96px; top: 138px; width: 102px; height: 32px; border-radius: 16px; background: rgba(60,60,60,0.85); color: var(--white); font-size: 11px; font-weight: 500; display: flex; align-items: center; justify-content: center; }

  .footer { position: absolute; left: 0; top: 950px; width: 1178px; height: 250px; background: var(--footer); }
  .foot-col { position: absolute; top: 25px; font-size: 12px; color: var(--ink); }
  .foot-col h4 { font-weight: 400; font-size: 12px; margin-bottom: 8px; white-space: nowrap; }
  .foot-col ul { list-style: none; font-size: 12px; color: var(--muted); }
  .foot-col li { line-height: 28px; }
  .mail-form { position: absolute; left: 848px; top: 48px; display: flex; gap: 10px; }
  .mail-input { width: 148px; height: 29px; border: 1px solid var(--line); background: var(--white); font-size: 12px; color: #aaa; padding: 6px; }
  .mail-join { width: 45px; height: 28px; border: 1px solid #bbb; border-radius: 3px; background: #e4e4e4; font-size: 11px; color: var(--ink); display: flex; align-items: center; justify-content: center; }
  .connect { position: absolute; left: 848px; top: 104px; font-size: 11px; color: var(--ink); }
  .connect-list { display: grid; grid-template-columns: repeat(3, auto); gap: 5px 10px; margin-top: 8px; font-size: 10px; }
  .connect-list span { display: flex; align-items: center; gap: 4px; }
  .dot { width: 8px; height: 8px; border-radius: 50%; background: #333; display: inline-block; }
  .foot-rule { position: absolute; left: 128px; top: 170px; width: 922px; height: 1px; background: var(--line); }
  .copyright { position: absolute; left: 128px; top: 202px; font-size: 12px; color: var(--muted); }
  .copyright b { color: var(--ink); font-weight: 400; }
  .payments { position: absolute; left: 632px; top: 194px; display: flex; gap: 14px; }
  .pay { width: 49px; height: 30px; background: var(--white); border: 1px solid var(--line); border-radius: 2px; font-size: 8px; color: var(--ink); display: flex; align-items: center; justify-content: center; }
</style>
</head>
<body>
  <header>
    <div class="topbar"></div>
    <span class="brand-name">Varenna</span>
    <span class="brand-tag">designer jewellery</span>
    <nav class="account-links">
      <a href="#">SIGN IN</a><span class="sep">|</span>
      <a href="#">MY ACCOUNT</a><span class="sep">|</span>
      <a href="#">MY WISHLIST</a><span class="sep">|</span>
      <a href="#">JOIN US</a>
    </nav>
    <div class="search">
      <svg width="20" height="16" viewBox="0 0 20 16"><circle cx="7" cy="7" r="5" fill="none" stroke="#999" stroke-width="2"/><line x1="11" y1="10" x2="17" y2="15" stroke="#999" stroke-width="2.5"/></svg>
    </div>
    <div class="utility">
      <svg width="17" height="14" viewBox="0 0 17 14"><path d="M1 5h15l-2 8H3z" fill="#555"/><path d="M5 5l3-4 3 4" fill="none" stroke="#555" stroke-width="1.3"/></svg>
      <span>SHOPPING BAG <b>(0)</b></span>
      <span>&nbsp;|&nbsp;</span>
      <span>FOLLOW US :</span>
      <span class="follow-names"><span>Chatterloop</span><span>Chirpwell</span><span>Boardquill</span><span>Snapfold</span></span>
      <svg width="13" height="10" viewBox="0 0 13 10"><rect x="0.5" y="0.5" width="12" height="9" fill="#111"/><path d="M1 1l5.5 5L12 1" fill="none" stroke="#fff"/></svg>
    </div>
  </header>

  <nav class="nav">
    <ul>
      <li>COLLECTION GALLERY <span class="caret"></span></li>
      <li>ABOUT US <span class="caret"></span></li>
      <li>BLOG <span class="caret"></span></li>
      <li>EDUCATION <span class="caret"></span></li>
      <li>BUYING FROM US <span class="caret"></span></li>
      <li>TESTIMONIALS</li>
      <li>24Hrs PRODUCT OFFERS</li>
    </ul>
  </nav>

  <section class="hero" role="img" aria-label="Platinum diamond engagement ring with pear-shaped side stones on a pale grey background">
    <ul class="submenu">
      <li>&rarr; RINGS</li>
      <li>&rarr; WATCHES</li>
      <li>&rarr; BRACELETS</li>
      <li>&rarr; EARRINGS</li>
    </ul>
    <a class="slide-arrow prev" href="#" aria-label="Previous slide"><svg width="56" height="56"><path d="M33 16L21 28l12 12" fill="none" stroke="#fff" stroke-width="2"/></svg></a>
    <a class="slide-arrow next" href="#" aria-label="Next slide"><svg width="56" height="56"><path d="M23 16l12 12-12 12" fill="none" stroke="#fff" stroke-width="2"/></svg></a>
    <div class="hero-copy">
      <p class="lead">We are</p>
      <p class="sub">designer jewellery maker &amp;<br>seller online.</p>
      <p class="note">We sell diamond jewellery too.</p>
    </div>
  </section>

  <section class="showcase">
    <svg class="showcase-arrow" style="left:96px" width="14" height="62"><path d="M12 1L2 31l10 30" fill="none" stroke="#777" stroke-width="1.5"/></svg>
    <div class="tile ring" role="img" aria-label="Emerald-cut diamond halo ring on black"></div>
    <div class="tile watch" role="img" aria-label="Gold diamond-set wristwatch">
      <span class="tile-label">WATCHES</span>
      <span class="quick-view">QUICK VIEW</span>
    </div>
    <div class="tile bracelet" role="img" aria-label="Diamond link bracelet on black"></div>
    <svg class="showcase-arrow" style="left:1070px" width="14" height="62"><path d="M2 1l10 30L2 61" fill="none" stroke="#777" stroke-width="1.5"/></svg>
  </section>

  <footer class="footer">
    <div class="foot-col" style="left:128px">
      <h4>CUSTOMER CARE</h4>
      <ul>
        <li>Product Information</li>
        <li>Shipping &amp; Delivery</li>
        <li>Returns &amp; Exchanges</li>
        <li>Privacy &amp; Security</li>
      </ul>
    </div>
    <div class="foot-col" style="left:317px"><h4>FAQ</h4></div>
    <div class="foot-col" style="left:412px"><h4>CONTACT US</h4></div>
    <div class="foot-col" style="left:547px"><h4>TERMS &amp; CONDITIONS</h4></div>
    <div class="foot-col" style="left:730px"><h4>SITE MAP</h4></div>
    <div class="foot-col" style="left:848px"><h4>JOIN E-MAIL LISTING</h4></div>
    <div class="mail-form">
      <div class="mail-input">Join our mailing list</div>
      <div class="mail-join">JOIN</div>
    </div>
    <div class="connect">
      CONNECT US
      <div class="connect-list">
        <span><i class="dot"></i>Chatterloop</span>
        <span><i class="dot"></i>Chirpwell</span>
        <span><i class="dot"></i>Boardquill</span>
        <span><i class="dot"></i>Reelhaven</span>
        <span><i class="dot"></i>Circlemoor</span>
        <span><i class="dot"></i>Snapfold</span>
      </div>
    </div>
    <div class="foot-rule"></div>
    <p class="copyright">Copyright &copy; 2013. <b>Varenna</b>. All Right Reserved</p>
    <div class="payments">
      <span class="pay">Amberline</span>
      <span class="pay">Farpoint</span>
      <span class="pay">Searchmoor</span>
      <span class="pay">Cardello</span>
      <span class="pay">Duoring</span>
      <span class="pay">CoinVeil</span>
      <span class="pay">Trevia</span>
    </div>
  </footer>
</body>
</html>
```